Counseling Practice Business Card

I need a professional looking business card incorporating my new logo that was just completed. Card needs to incorporate my name and title, description of my specialty, my address, my phone number, my fax number, my email and my website URL. I need to be able to choose design on/with different paper colors and textures.
I do not have a lot of business card ideas so I am open to anything but I want bold,sharp, clear card without additional designs other than my logo (see attached file info). I am open to different color backgrounds or paper colors including black. I do not like traditional brackets around area codes in phone number or dashes between numbers in phone number. Am open to other ways of presenting including periods between numbers as appropriate. I do not know enough to know what I like yet but I want card to coordinate and work together with my logo. My practice emphasizes natural mental health interventions so any use of color (with background paper color or the blue and green in my logo) that elicits nature is nice. In addition to black, any natural brown or wood looking background might be desirable also. Most of the offerings so far look very similar and boring.

Target Market(s)

Potential therapy clients and other professionals

Contact Information for Business Card

Card information:
Gerald M. Whitcombe, Ph.D.
Licensed Clinical Psychologist
Integrative Health Coach
4812 Marlowe Ridge Blvd SE
Suite 310
Alder Falls, OR 97402
(555) 415-2983 phone
(555) 581-4096 fax
drgeraldwhitcombe@quillmarsh.net
brightfernwellness.net

Font styles to use
Serif
Sans Serif
Other font styles liked:
• anything that you think looks crisp, clear and easily readable

Requirements
Must have
• Any color used should coordinate with my logo design (see attached files).
• Card should be printed horizontally so top and bottom are longest sides of rectangle.
• Background color or paper color should complement and highlight logo. Do not like a white background. black, grey, brown or any color my logo would blend well with.
Nice to have
• I would like designer to utilize color to highlight letters/name or phone-fax-web symbols.
• Bottom edge of card could be highlighted if appropriate to an idea.
Should not have
• I would NOT want the card to have a pure white background at all.
• No clear cards.
• Cards should be oriented with long sides on bottom and top, NOT sides. DO NOT LIKE THIS THIN TALL ORIENTATION.

```html
<!DOCTYPE html>
<html lang="en">
<head>
<meta charset="utf-8">
<title>Brightfern Wellness – Business Card</title>
<link rel="stylesheet" href="https://fonts.googleapis.com/css2?family=Open+Sans:wght@400;600&family=Roboto+Condensed:wght@700&display=swap">
<style>
  :root {
    --backdrop: #2b2b2b;
    --card-black: #141414;
    --brand-blue: #2a74b8;
    --brand-green: #0b7a3c;
    --text-white: #ffffff;
    --text-grey: #b9b9b9;
  }
  * { margin: 0; padding: 0; box-sizing: border-box; }
  html, body { width: 1200px; height: 960px; overflow: hidden; }
  body {
    background: var(--backdrop);
    position: relative;
    font-family: "Open Sans", Arial, sans-serif;
  }
  .card {
    position: absolute;
    left: 322px;
    width: 598px;
    height: 342px;
    background: var(--card-black);
    overflow: hidden;
  }
  .card--front { top: 108px; }
  .card--back { top: 493px; }

  .card__swoosh { position: absolute; inset: 0; width: 100%; height: 100%; }

  .practice-name {
    position: absolute;
    font-family: "Open Sans", Arial, sans-serif;
    font-weight: 600;
    color: var(--brand-blue);
    white-space: nowrap;
    letter-spacing: 0.5px;
  }
  .card--front .practice-name { left: 38px; top: 78px; font-size: 27px; }
  .card--back .practice-name {
    left: 0; right: 0; top: 142px; text-align: center; font-size: 42px;
  }

  .contact {
    position: absolute;
    right: 20px;
    top: 154px;
    text-align: right;
    color: var(--text-white);
    font-size: 14.5px;
    line-height: 19.5px;
  }
  .contact__name {
    font-family: "Roboto Condensed", "Arial Narrow", sans-serif;
    font-weight: 700;
    font-size: 20px;
    line-height: 26px;
    text-transform: uppercase;
  }
  .contact__titles { margin-bottom: 6px; line-height: 21px; }
  .contact__line { display: flex; justify-content: flex-end; align-items: center; gap: 5px; }
  .contact__icon { width: 13px; height: 13px; fill: var(--text-white); flex: none; }
  .contact__address { margin-top: 4px; font-size: 14px; }

  .back-url {
    position: absolute;
    left: 0; right: 0; top: 284px;
    text-align: center;
    color: var(--text-grey);
    font-size: 14px;
    letter-spacing: 4px;
  }
</style>
</head>
<body>

<section class="card card--front" aria-label="Business card front">
  <svg class="card__swoosh" viewBox="0 0 598 342" preserveAspectRatio="none" aria-hidden="true">
    <path d="M423 0 L598 0 L598 342 L78 342 C250 250 430 150 423 0 Z" fill="var(--brand-blue)"/>
    <path d="M395 0 L423 0 C430 150 250 250 78 342 C240 240 412 140 395 0 Z" fill="var(--brand-green)"/>
  </svg>

  <div class="practice-name">Brightfern Wellness</div>

  <div class="contact">
    <div class="contact__name">Gerald M. Whitcombe, Ph.D.</div>
    <div class="contact__titles">Licensed Clinical Psychologist<br>Integrative Health Coach</div>
    <div class="contact__line">(555) 415-2983
      <svg class="contact__icon" viewBox="0 0 16 16" aria-hidden="true"><path d="M1 5 C1 2 15 2 15 5 L15 7 L11 7 L11 5 L5 5 L5 7 L1 7 Z M3 9 L13 9 L14 14 L2 14 Z"/></svg>
    </div>
    <div class="contact__line">(555) 581-4096
      <svg class="contact__icon" viewBox="0 0 16 16" aria-hidden="true"><path d="M4 1 H12 V5 H4 Z M1 6 H15 V12 H12 V10 H4 V12 H1 Z M5 11 H11 V15 H5 Z"/></svg>
    </div>
    <div class="contact__line">drgeraldwhitcombe@quillmarsh.net
      <svg class="contact__icon" viewBox="0 0 16 16" aria-hidden="true"><path d="M1 3 H15 V4 L8 9 L1 4 Z M1 5.5 L8 10.5 L15 5.5 V13 H1 Z"/></svg>
    </div>
    <div class="contact__line">www.brightfernwellness.net
      <svg class="contact__icon" viewBox="0 0 16 16" aria-hidden="true"><circle cx="8" cy="8" r="7"/><path d="M5 4 L8 6 L7 9 L4 8 Z M10 9 L12 11 L10 13 Z" fill="var(--brand-blue)"/></svg>
    </div>
    <div class="contact__address">4812 Marlowe Ridge Blvd SE, Suite 310, Alder Falls, OR 97402</div>
  </div>
</section>

<section class="card card--back" aria-label="Business card back">
  <div class="practice-name">Brightfern Wellness</div>
  <div class="back-url">www.brightfernwellness.net</div>
</section>

</body>
</html>
```